Direct to Consumer extended service contract business with a new disruptive business model needs a

We need a customized wordpress design for a company called 'Bright Harbor Assurance'.
We provide an innovative and unique service contract protection program direct to consumers. This program provides monthly coverage for all electronics purchased in the last 4 years and all electronics the consumer purchases in the future for a low monthly fee. The overall design should communicate a sense of legitimacy, ethics, and superior customer service and support (in an industry that has a huge PR issue to overcome).
Electronics is the first product group, other product groups with different price points to launch in the future..

Target Market(s)

All purchasers of electronic goods...all demographics

Industry/Entity Type

Electronics

Font styles to use
Sans Serif

Requirements
Must have
• Customer Testimonials
Industry News
Customer ratings
Blog posts
Call to action messaging
Like the functional elements and design of quillmesa.example (need to be better)
Nice to have
• Like to see video testimonials
Social network "whats trending related to electronics or service contract industry"
Easy way to register products for warranty

```html
<!DOCTYPE html>
<html lang="en">
<head>
<meta charset="utf-8">
<title>Bright Harbor Assurance</title>
<link href="https://fonts.googleapis.com/css2?family=Open+Sans:wght@400;600;700;800&display=swap" rel="stylesheet">
<style>
:root{
  --green:#3aa845;
  --green-bright:#4cc057;
  --ink:#3a3d40;
  --muted:#7c7f82;
  --hero-bg:#eef0ef;
  --white:#ffffff;
  --dark:#1c1f21;
  --dark-2:#2b3034;
  --line:#cfd2d3;
}
*{box-sizing:border-box;margin:0;padding:0}
html,body{width:1200px;height:3261px;overflow:hidden}
body{font-family:"Open Sans",Arial,sans-serif;color:var(--ink);background:var(--white)}
.section{position:absolute;left:0;width:1200px;overflow:hidden}
.menu-btn{position:absolute;width:48px;height:50px;display:flex;flex-direction:column;justify-content:center;align-items:center;gap:6px}
.menu-btn span{display:block;width:22px;height:3px;background:var(--green-bright)}
.menu-btn.light{background:#cfe8d1}
.menu-btn.light span{background:var(--green)}
.menu-btn.dark{background:#1a1c1d}
.side-dots{position:absolute;left:157px;display:flex;flex-direction:column;gap:12px}
.side-dots i{display:block;width:12px;height:12px;border-radius:50%;border:1.5px solid #b9bcbe}
.side-dots i.on{background:var(--green);border-color:var(--green)}
.dark-sec .side-dots i{border-color:#8c9092}
.section-title{position:absolute;left:196px;font-weight:800;font-size:42px;letter-spacing:-.5px;white-space:nowrap}
.section-title b{color:var(--green);font-weight:800}

/* hero */
.hero{top:0;height:652px;background:var(--hero-bg)}
.brand{position:absolute;left:196px;top:70px;display:flex;align-items:center;gap:10px}
.brand-mark{width:34px;height:34px;background:var(--green)}
.brand-name{font-size:20px;font-weight:700;color:var(--green)}
.hero-title{position:absolute;left:196px;top:206px;font-size:50px;font-weight:800;color:var(--ink);letter-spacing:-.5px;white-space:nowrap}
.hero-title b{color:var(--green)}
.hero-sub{position:absolute;left:196px;top:290px;font-size:17px;line-height:43px;color:var(--green);letter-spacing:.5px;white-space:nowrap}
.btn{position:absolute;left:238px;top:404px;width:173px;height:53px;background:var(--green);color:#fff;font-weight:600;font-size:17px;display:flex;align-items:center;justify-content:center}
.devices{position:absolute;left:560px;top:287px;width:435px;height:262px;background:linear-gradient(135deg,#d9dcdd,#9ea3a6 55%,#3c4043);border-radius:6px}
.badge{position:absolute;top:560px;height:70px;border-radius:10px}
.badge.one{left:405px;width:108px;background:#2f3234}
.badge.two{left:606px;width:186px;background:#f3c14a;border-radius:36px}

/* about */
.about{top:652px;height:653px;background:var(--white)}
.about-list{position:absolute;left:200px;top:205px;list-style:none;font-size:11.5px;line-height:25px;color:#555;white-space:nowrap}
.about-list li::before{content:"✓ ";color:var(--green);font-weight:700}
.about-list .cont{padding-left:14px}
.about-list .cont::before{content:""}
.about-quote{position:absolute;left:625px;top:222px;width:300px;font-size:15px;line-height:24px;color:#a5a8aa}
.about-quote cite{display:block;margin-top:26px;font-style:normal}
.about-devices{position:absolute;left:238px;top:408px;width:636px;height:238px;background:linear-gradient(180deg,#e6e8e9,#b4b8ba 60%,#55595c);border-radius:4px}

/* services */
.services{top:1304px;height:653px;background:linear-gradient(180deg,#33393d,#1d2124 55%,#111314);color:#fff}
.services .section-title{top:131px;color:#fff}
.title-note{position:absolute;left:500px;top:138px;padding-left:22px;border-left:2px solid #9ca0a2;font-size:15px;line-height:38px;color:#d8dadb;white-space:nowrap}
.service{position:absolute;top:270px;width:250px}
.service-icon{position:absolute;left:0;top:6px;width:40px;height:40px;background:var(--green);display:flex;align-items:center;justify-content:center}
.service-icon.ghost{background:transparent}
.service h3{margin-left:60px;font-size:20px;font-weight:800;line-height:26px;text-transform:uppercase}
.service p{margin-left:60px;margin-top:10px;font-size:12.5px;line-height:20px;color:#c9cccd}

/* testimonials */
.testimonials{top:1957px;height:652px;background:var(--white)}
.testimonials .section-title{top:92px;color:var(--green)}
.arrow{position:absolute;top:101px;width:30px;height:30px;border-radius:50%;border:1.5px solid #b0b3b5;display:flex;align-items:center;justify-content:center}
.arrow.on{border-color:var(--ink)}
.video{position:absolute;left:189px;top:247px;width:284px;height:154px;background:linear-gradient(180deg,#7f9cb8,#3d4a52 60%,#151a1d)}
.play{position:absolute;left:125px;top:60px;width:36px;height:36px;border-radius:50%;background:rgba(0,0,0,.55);display:flex;align-items:center;justify-content:center}
.video-bar{position:absolute;left:0;bottom:0;width:100%;height:18px;background:rgba(0,0,0,.7)}
.who{position:absolute;right:196px;top:240px;text-align:right}
.who h4{font-size:22px;font-weight:700;color:var(--green)}
.who span{font-size:11px;color:#999}
.quote-mark{position:absolute;left:492px;top:282px;font-size:34px;color:#bfc2c4;font-weight:700}
.quote-text{position:absolute;left:518px;top:286px;width:486px;font-size:12.5px;line-height:20px;color:#666}

/* contact */
.contact{top:2609px;height:652px;background:linear-gradient(180deg,#1b1d1f,#232628 60%,#151617);color:#fff}
.contact .section-title{top:92px;color:#fff}
.contact .title-note{left:466px;top:98px;border:none;padding-left:16px;font-size:13px}
.contact-intro{position:absolute;left:196px;top:172px;width:810px;font-size:12px;line-height:20px;color:#d2d4d5}
.info{position:absolute;left:196px;width:270px}
.info-icon{position:absolute;left:0;top:0;width:48px;height:48px;background:var(--green);display:flex;align-items:center;justify-content:center}
.info h5{margin-left:74px;font-size:20px;font-weight:800;text-transform:uppercase;white-space:nowrap}
.info p{margin-left:74px;font-size:11.5px;line-height:17px;color:#c7c9ca}
.field{position:absolute;height:43px;border:1.5px solid #8d9193;font-size:13px;color:#b6b9ba;padding:10px 14px}
.copyright{position:absolute;left:0;width:1200px;top:596px;text-align:center;font-size:13px;color:#d9dbdc}
</style>
</head>
<body>

<section class="section hero">
  <div class="brand"><span class="brand-mark"></span><span class="brand-name">Bright Harbor Assurance</span></div>
  <div class="menu-btn light" style="left:955px;top:30px"><span></span><span></span><span></span></div>
  <h1 class="hero-title"><b>BRIGHT HARBOR</b> ASSURANCE</h1>
  <p class="hero-sub">A REVOLUTIONARY PROTECTION<br>COMPANY IN THE WORLD</p>
  <div class="side-dots" style="top:280px"><i class="on"></i><i></i><i></i><i></i></div>
  <a class="btn">Sign Up Now</a>
  <div class="devices" role="img" aria-label="Group of electronic devices: desktop monitor, laptop, tablet and phone"></div>
  <div class="badge one" role="img" aria-label="Privacy certification badge"></div>
  <div class="badge two" role="img" aria-label="Security certification badge"></div>
</section>

<section class="section about">
  <div class="menu-btn dark" style="left:946px;top:33px"><span></span><span></span><span></span></div>
  <h2 class="section-title" style="top:128px"><b>ABOUT</b> US</h2>
  <ul class="about-list">
    <li>NO LIMIT to the number of products covered</li>
    <li>Coverage NEVER ends</li>
    <li>Electronics purchased up to 4 years prior to your sign-up date are</li>
    <li class="cont">eligible</li>
    <li>Over 10,000 nationwide service centers</li>
    <li>Registering all your products takes less than 20 minutes</li>
    <li>All for just $29.97 per month plus a one-time $30 Membership Fee</li>
  </ul>
  <div class="side-dots" style="top:282px;gap:10px"><i></i><i class="on"></i><i></i><i></i></div>
  <blockquote class="about-quote">"The Average U.S. Household has about 40 Electronic Gadgets."<cite>- Home Tech Research Group</cite></blockquote>
  <div class="about-devices" role="img" aria-label="Household electronics: printer, television, computers, tablet, phone and laptop"></div>
</section>

<section class="section services dark-sec" role="img" aria-label="Dimmed photo of a desk with electronics behind the services section">
  <div class="menu-btn dark" style="left:946px;top:33px"><span></span><span></span><span></span></div>
  <h2 class="section-title"><b>OUR</b> SERVICES</h2>
  <p class="title-note">We provide the best electronics protection</p>
  <div class="side-dots" style="top:280px;gap:10px"><i></i><i></i><i class="on"></i><i></i></div>
  <div class="service" style="left:202px">
    <div class="service-icon"><svg width="22" height="18" viewBox="0 0 22 18"><rect x="1" y="1" width="20" height="16" fill="none" stroke="#fff" stroke-width="2"/><path d="M1 6h20" stroke="#fff" stroke-width="2"/></svg></div>
    <h3>Superior Coverage</h3>
    <p>Every device in your home is covered from day one, with no limit on the number of products and no hidden exclusions.</p>
  </div>
  <div class="service" style="left:473px">
    <div class="service-icon ghost"><svg width="30" height="30" viewBox="0 0 30 30"><path d="M25 15a10 10 0 1 1-3-7" fill="none" stroke="#4cc057" stroke-width="3"/><path d="M23 3v6h-6" fill="none" stroke="#4cc057" stroke-width="3"/></svg></div>
    <h3>Revolutionary Protection</h3>
    <p>One simple monthly plan protects what you bought in the last four years and everything you will buy in the future.</p>
  </div>
  <div class="service" style="left:757px">
    <div class="service-icon ghost"><svg width="30" height="30" viewBox="0 0 30 30"><circle cx="15" cy="15" r="6" fill="none" stroke="#4cc057" stroke-width="3"/><path d="M15 2v5M15 23v5M2 15h5M23 15h5M6 6l3.5 3.5M20.5 20.5L24 24M6 24l3.5-3.5M20.5 9.5L24 6" stroke="#4cc057" stroke-width="3"/></svg></div>
    <h3>Customer Service</h3>
    <p>Real people answer your call around the clock, and most claims are registered and settled in under twenty minutes.</p>
  </div>
</section>

<section class="section testimonials">
  <div class="menu-btn dark" style="left:946px;top:33px"><span></span><span></span><span></span></div>
  <h2 class="section-title">TESTIMONIALS</h2>
  <div class="arrow" style="left:931px"><svg width="10" height="12" viewBox="0 0 10 12"><path d="M7 1L2 6l5 5" fill="none" stroke="#b0b3b5" stroke-width="2"/></svg></div>
  <div class="arrow on" style="left:970px"><svg width="10" height="12" viewBox="0 0 10 12"><path d="M3 1l5 5-5 5" fill="none" stroke="#3a3d40" stroke-width="2"/></svg></div>
  <div class="side-dots" style="top:280px;gap:10px"><i></i><i></i><i></i><i class="on"></i><i></i></div>
  <div class="video" role="img" aria-label="Video testimonial still of a lakeside landscape">
    <div class="play"><svg width="14" height="16" viewBox="0 0 14 16"><path d="M2 1l11 7-11 7z" fill="#fff"/></svg></div>
    <div class="video-bar"></div>
  </div>
  <div class="who"><h4>Marcus Ellery</h4><span>Manager, Orchard Lane Co.</span></div>
  <span class="quote-mark">“</span>
  <p class="quote-text">I signed up after my laptop failed just outside the store warranty. Registering my devices took minutes, and when my television broke the claim was approved the same day. The monthly fee is lower than a single repair, and the support team treated me with real respect from start to finish. I recommend it to everyone I know.</p>
</section>

<section class="section contact dark-sec">
  <div class="menu-btn dark" style="left:946px;top:42px"><span></span><span></span><span></span></div>
  <h2 class="section-title"><b>CONTACT</b> US</h2>
  <p class="title-note">Do you have any query?</p>
  <p class="contact-intro">The days of costly, store-bought extended warranties are coming to an end. Bright Harbor Assurance is changing the service and repair industry. Instead of paying for each product, you pay one low monthly fee, and every electronic device you own, old or new, is protected. Send us your question and our team will reply within one business day.</p>
  <div class="side-dots" style="top:285px;gap:10px"><i></i><i></i><i></i><i></i><i class="on"></i></div>
  <div class="info" style="top:280px">
    <div class="info-icon"><svg width="20" height="26" viewBox="0 0 20 26"><path d="M10 25S1 14 1 9a9 9 0 0 1 18 0c0 5-9 16-9 16z" fill="#fff"/><circle cx="10" cy="9" r="3.5" fill="#3aa845"/></svg></div>
    <h5>Address</h5><p>48 Linden Row, Suite 12,<br>Fairport, NY 14450</p>
  </div>
  <div class="info" style="top:365px">
    <div class="info-icon"><svg width="22" height="22" viewBox="0 0 22 22"><path d="M5 1l4 5-2 3c1 3 3 5 6 6l3-2 5 4-2 4C10 21 1 12 1 3z" fill="#fff"/></svg></div>
    <h5>Phone Number</h5><p>+1 555 014 2290 / 555 014 2291</p>
  </div>
  <div class="info" style="top:456px">
    <div class="info-icon"><svg width="24" height="18" viewBox="0 0 24 18"><rect x="1" y="1" width="22" height="16" fill="#fff"/><path d="M1 1l11 9 11-9" fill="none" stroke="#3aa845" stroke-width="2"/></svg></div>
    <h5>Email</h5><p>hello@brightharbor.example</p>
  </div>
  <div class="field" style="left:473px;top:280px;width:260px">First name</div>
  <div class="field" style="left:748px;top:280px;width:253px">Last name</div>
  <div class="field" style="left:473px;top:342px;width:260px">Email</div>
  <div class="field" style="left:748px;top:342px;width:253px">Query Type</div>
  <div class="field" style="left:473px;top:398px;width:528px;height:130px">Your Message....</div>
  <p class="copyright">Copyright© 2014. All rights reserved.</p>
</section>

</body>
</html>
```